Zielgruppe
Die Velorin Akademie bietet Kurse, Seminare & Coachings im Bereich der Kommunikation / Persönlichkeitsentwicklung an.
Folgendes Angebot besteht zur Zeit:
Seminare:
- 'Erste Schritte im Dialog', eine Einführung in die Kommunikation.
- 'Heitere Töchter, ruhige Väter' zum Thema Erziehung.
- 'Reifen mit Gelassenheit', zum Thema Älter werden und den Umgang damit.
Kurse:
- 'Gewaltfreie Kommunikation', Übungsgruppe
Coaching:
- Einzelsitzungen mit Hypnose
Ps: im Anhang unter 'Angabot_Vorlage.pdf' finden Sie mehr Infos zu den einezlenen Angebote.
Aufgabenstellung
Bitte berücksichtigen Sie, dass bereits ein Logo besteht (siehe Anhang).
Vom gesamteindruck her sollte die Website aufgeräumt, übersichtlich, harmonisch, freundlich & frisch wirken.
Es wäre super, wenn die Website authentisch wirkt (und weniger '0815 Business Website').
Bitte bedenken Sie, dass die Website sich an Private richtet, die sich nach einem 'strahlenderen & unbeschwerterem Lebene sehnen'.
Wir haben bereits viele Persönlichkeiten stärken können und möchten dies auch witerhin mit viel Herzblut machen.

```html
<!DOCTYPE html>
<html lang="de">
<head>
<meta charset="utf-8">
<title>Velorin Akademie – Angebot</title>
<link rel="stylesheet" href="https://fonts.googleapis.com/css2?family=Raleway:wght@300;400;500;600;700&display=swap">
<style>
:root{
  --canvas:#ede5e0;
  --page:#ffffff;
  --section:#f8f5f3;
  --ink:#333333;
  --muted:#8a8a8a;
  --accent:#f29a72;
  --accent-soft:#f7b59a;
  --peach:#f9dccb;
  --plum:#665870;
  --plum-light:#83747b;
  --cta:#f26b3a;
  --footer-bar:#d9d1cb;
}
*{box-sizing:border-box;margin:0;padding:0}
html,body{width:1200px;height:3561px;overflow:hidden}
body{position:relative;background:var(--canvas);font-family:'Raleway',sans-serif;color:var(--ink)}
.a{position:absolute}
.page{left:135px;top:76px;width:938px;height:3408px;background:var(--page)}
.nav-brand{left:166px;top:96px;font-size:13px;font-weight:600;letter-spacing:2px}
.nav-link{top:102px;font-size:12px;font-weight:500;letter-spacing:.5px}
.nav-active{border:1px solid var(--cta);color:var(--cta);padding:2px 10px;top:98px}
.hero{left:135px;top:135px;width:938px;height:491px;background:radial-gradient(ellipse at 52% 78%,#f3d7b8 0%,#c9b7c4 28%,#9aa5bc 60%,#7f8aa3 100%)}
.hero-title{left:135px;width:938px;top:410px;text-align:center;color:#fff;font-size:38px;font-weight:400;letter-spacing:8px}
.hero-tag{left:135px;width:938px;top:472px;text-align:center;color:#fff;font-size:19px;font-weight:400;letter-spacing:2px}
.hero-arrow{top:337px}
.dot{top:601px;width:8px;height:8px;border:1px solid #fff;border-radius:50%}
.newsletter{left:135px;top:643px;width:938px;height:62px;background:var(--peach)}
.nl-text{left:271px;top:658px;color:#fff;font-size:12px;line-height:16px;font-weight:500}
.field{background:#fff;border:1px solid #ddd;font-size:9px;letter-spacing:1px;color:#aaa;padding-left:10px;display:flex;align-items:center}
.btn{background:var(--accent-soft);color:#fff;font-size:11px;letter-spacing:1.5px;display:flex;align-items:center;justify-content:center;font-weight:500}
.section-title{left:135px;width:938px;top:774px;text-align:center;font-size:27px;letter-spacing:1.5px;color:#6e6e6e;font-weight:400}
.offer{left:135px;width:938px;background:var(--section)}
.photo{background:linear-gradient(135deg,#d2d2d2,#8f8f8f)}
.offer-title{font-size:16px;font-weight:600;color:#666}
.fact-label,.fact-value{font-size:12.5px;font-weight:600;color:var(--accent);letter-spacing:.5px}
.copy{font-size:11px;line-height:15px;color:#777;width:792px}
.agenda-h{font-size:17px;font-weight:500;color:#777}
.ag-label{font-size:12.5px;font-weight:600;color:var(--accent)}
.ag-text{font-size:11px;line-height:15px;color:#777}
.scene{left:134px;top:2795px;width:937px;height:260px;background:linear-gradient(180deg,#c7c6c8 0%,#e2dcd6 45%,#8e8985 100%)}
.f-brand{left:185px;width:295px;top:3120px;text-align:center;font-size:22px;letter-spacing:3px;color:#666}
.f-line{left:185px;width:295px;text-align:center;font-size:13px;color:#777}
.f-head{left:623px;top:3086px;font-size:12.5px;letter-spacing:1px;color:#777;line-height:16px}
.bottom-bar{left:135px;top:3404px;width:938px;height:80px;background:var(--footer-bar)}
.bar-text{top:3440px;font-size:12.5px;color:#fff;letter-spacing:.5px}
.veil{left:0;top:0;width:1200px;height:3561px;background:rgba(255,255,255,.55)}
.modal{left:326px;top:1807px;width:586px;height:506px;box-shadow:0 4px 10px rgba(0,0,0,.3);color:#fff}
.m-head{left:0;top:0;width:586px;height:95px;background:var(--plum)}
.m-title{left:0;width:586px;top:38px;text-align:center;font-size:27px;letter-spacing:3px;font-weight:500}
.m-close{left:561px;top:8px;font-size:15px}
.m-facts{left:0;top:95px;width:586px;height:134px;background:var(--plum-light)}
.m-strip{left:0;top:229px;width:586px;height:22px;background:var(--plum)}
.m-form{left:0;top:251px;width:586px;height:172px;background:var(--plum-light)}
.m-foot{left:0;top:423px;width:586px;height:83px;background:var(--plum)}
.m-label,.m-value{font-size:13px;font-weight:600;letter-spacing:.5px}
.m-field{background:#fff;font-size:7px;letter-spacing:.5px;color:#777;padding-left:6px;display:flex;align-items:center}
.m-note{font-size:6px}
.m-btn{background:var(--cta);color:#fff;font-size:12px;letter-spacing:1px;display:flex;align-items:center;justify-content:center;font-weight:500}
</style>
</head>
<body>
<div class="a page"></div>

<div class="a nav-brand">VELORIN AKADEMIE</div>
<div class="a nav-link" style="left:708px">HOME</div>
<div class="a nav-link nav-active" style="left:775px">ANGEBOT</div>
<div class="a nav-link" style="left:876px">KONTAKT</div>
<div class="a nav-link" style="left:962px">ÜBER UNS</div>

<div class="a hero" role="img" aria-label="Sternenhimmel über einem Bergtal mit einer Gruppe jubelnder Menschen"></div>
<div class="a hero-title">VELORIN AKADEMIE</div>
<div class="a hero-tag">NEUE PERSPECTIVEN • NEUE HORIZONTE</div>
<svg class="a hero-arrow" style="left:156px" width="22" height="40" viewBox="0 0 22 40"><path d="M20 2 L3 20 L20 38" fill="none" stroke="#fff" stroke-width="2"/></svg>
<svg class="a hero-arrow" style="left:1032px" width="22" height="40" viewBox="0 0 22 40"><path d="M2 2 L19 20 L2 38" fill="none" stroke="#fff" stroke-width="2"/></svg>
<div class="a dot" style="left:585px"></div>
<div class="a dot" style="left:598px;background:#fff"></div>
<div class="a dot" style="left:611px"></div>

<div class="a newsletter"></div>
<div class="a nl-text">KOSTENLOSES ERSTGESPRÄCH<br>Abonnieren Sie unseren Newsletter!</div>
<div class="a field" style="left:542px;top:660px;width:329px;height:27px">E-MAIL ADRESSE</div>
<div class="a btn" style="left:885px;top:662px;width:39px;height:24px">OK</div>

<div class="a section-title">UNSERE AKTUELLE ANGEBOTE</div>

<!-- Angebot 1 -->
<div class="a offer" style="top:853px;height:907px"></div>
<div class="a photo" style="left:184px;top:899px;width:272px;height:246px" role="img" aria-label="Schwarzweissfoto einer Familie, die Hand in Hand über eine Brücke geht"></div>
<div class="a offer-title" style="left:512px;top:897px">SEMINAR: Heitere Töchter, ruhige Väter</div>
<div class="a fact-label" style="left:512px;top:939px">ZIEL</div><div class="a fact-value" style="left:593px;top:939px">Entspanntes und erfülltes Leben mit Kinder</div>
<div class="a fact-label" style="left:512px;top:971px">DAUER</div><div class="a fact-value" style="left:593px;top:971px">4 Abende à 1.5 Stunden</div>
<div class="a fact-label" style="left:512px;top:1003px">KOSTEN</div><div class="a fact-value" style="left:593px;top:1003px">CHF 280.-</div>
<div class="a fact-label" style="left:512px;top:1036px">ORT</div><div class="a fact-value" style="left:593px;top:1036px">Basel, Saal Lindenhof</div>
<div class="a fact-label" style="left:512px;top:1068px">DATUM</div><div class="a fact-value" style="left:593px;top:1068px">7.-11. Mai 2019.</div>
<div class="a btn" style="left:512px;top:1114px;width:125px;height:31px">ANMELDEN</div>
<p class="a copy" style="left:184px;top:1190px"><i>„Unter Erziehung versteht man die pädagogische Einflussnahme auf die Entwicklung und das Verhalten Heranwachsender“.</i> Erziehungstheorien gibt es unzählige, die das Spektrum von streng und autoritär bis hin zum Laisser-faire decken. Das selbst erlebte wird z.T. auch unreflektiert wiederholt und/oder wir verlieren uns in unzählige Ratgeber.</p>
<p class="a copy" style="left:184px;top:1252px">Mithilfe der Neurowissenschaften wird uns klar, dass das oft kräftezerrende Ringen rund um die Erziehung absolut unnötig und überflüssig ist, ja sogar schädigend. Am wirksamsten und effektivsten begleiten wir die Entwicklung eines Kindes mit Beziehung und Selbst-Erziehung – das ist die magische Formel. Indem wir zu nachahmenswerten Erwachsenen werden, fördern wir unsere eigene Persönlichkeitsentwicklung und ermöglichen damit eine harmonische, authentische und unterstützende Umgebung für die Kinder im z. Teil gehen wir der Frage nach, wie Eltern ihre Kindern verhelfen zu starken, selbstsicheren und erfüllten Erwachsenen zu werden, die ihren eigenen Platz in der Gesellschaft kreieren – jenseits von Konkurrenzkampf und Studiumsinflation.</p>
<div class="a agenda-h" style="left:184px;top:1385px">AGENDA</div>
<div class="a ag-label" style="left:185px;top:1426px">1. ABEND</div>
<div class="a ag-text" style="left:271px;top:1426px">• Lorem ipsum dolor sit amet<br>• In wisi facilisis vel, cum ut praesent dignissim<br>• Quem explicari ne mei. An mei mazim facilisis, vel ut munere postea putent, cu nulla melius omittam eum.</div>
<div class="a ag-label" style="left:185px;top:1488px">2. ABEND</div>
<div class="a ag-text" style="left:271px;top:1488px">• Lorem ipsum dolor sit amet<br>• In wisi facilisis vel, cum ut praesent dignissim<br>• Quem explicari ne mei<br>• An mei mazim facilisis, vel ut munere postea putent, cu nulla melius omittam eum.</div>
<div class="a ag-label" style="left:185px;top:1564px">3. ABEND</div>
<div class="a ag-text" style="left:277px;top:1564px">• In wisi facilisis vel, cum ut praesent dignissim<br>• Quem explicari ne mei<br>• Putent, cu nulla melius omittam eum</div>
<div class="a ag-label" style="left:185px;top:1625px">4. ABEND</div>
<div class="a ag-text" style="left:271px;top:1625px">• Lorem ipsum dolor sit amet<br>• In wisi facilisis vel, cum ut praesent dignissim<br>• Quem explicari ne mei. An mei mazim facilisis, vel ut munere postea putent, cu nulla melius omittam eum.</div>
<div class="a btn" style="left:538px;top:1706px;width:126px;height:32px">ANMELDEN</div>

<!-- Angebot 2 -->
<div class="a offer" style="top:1797px;height:950px"></div>
<div class="a photo" style="left:187px;top:1847px;width:200px;height:246px;background:linear-gradient(135deg,#e6e6e6,#9c9c9c)" role="img" aria-label="Schwarzweissfoto einer Armbanduhr"></div>
<div class="a fact-value" style="left:915px;top:1883px">Deinem Leben“</div>
<p class="a copy" style="left:184px;top:2130px">Zeit ist ein allgegenwärtiges Thema, das uns täglich begleitet. Was bedeutet uns doch Zeit?<br>Wie und wo nehmen wir sie wahr, und wie könnten wir die gewonnenen Jahre steigern –<br>könnten? Mit welchen Fragen beschäftigen wir uns?</p>
<p class="a copy" style="left:184px;top:2192px">Wir setzen uns mit unseren Vorstellungen auseinander und den Erkenntnissen der Wissenschaften<br>gegenüber. Aus der passiven Haltung wird eine bewusste Wahl.</p>
<p class="a copy" style="left:184px;top:2232px"><i>„Älter werden ist unumgänglich, alt sein nicht“</i></p>
<div class="a agenda-h" style="left:184px;top:2293px">AGENDA</div>
<div class="a ag-label" style="left:185px;top:2335px">1. BLOCK</div>
<div class="a ag-text" style="left:304px;top:2335px">08:00 - 10:00<br>Was ist Zeit? Die Erfindung der Zeit.<br>Wie hat dieser begriff unser Bewusstsein geprägt, mit welchen Folgen?</div>
<div class="a ag-label" style="left:185px;top:2397px">2. BLOCK</div>
<div class="a ag-text" style="left:304px;top:2397px">10:00-12:00<br>Wo finden wir aus der Zeit heraus? Wo gibt es keine Zeit?<br>Praktische Übung_ Achtsamkeit</div>
<div class="a ag-label" style="left:185px;top:2459px">MITTAGSPAUSE</div>
<div class="a ag-text" style="left:304px;top:2459px">12:00 - 13:30</div>
<div class="a ag-label" style="left:185px;top:2512px">3. BLOCK</div>
<div class="a ag-text" style="left:302px;top:2512px">13:30 - 15:30<br>Bezug von Zeit und Alter – unsere Vorstellungen wahrnehmen.<br>Ist altern ein naturgegebener Prozess dem wir unterworfen sind oder können wir es steuern? Wir gehen der Frage nach,<br>wie eine differenzierte und bewusst gewählte Auffassung von Zeit und älter werden sich auswirken.</div>
<div class="a ag-label" style="left:185px;top:2583px">4. BLOCK</div>
<div class="a ag-text" style="left:302px;top:2583px">15:30 - 17:00<br>Bahnbrechende Aussichten.<br>Fazit: Für welches altern entscheiden wir uns?<br>Dankbarkeit und Fülle</div>
<div class="a btn" style="left:538px;top:2683px;width:126px;height:31px">ANMELDEN</div>

<div class="a scene" role="img" aria-label="Person sitzt bei Sonnenaufgang auf einem Felsen über einem nebligen Tal"></div>

<!-- Footer -->
<div class="a f-brand">VELORIN AKADEMIE</div>
<div class="a f-line" style="top:3228px;font-weight:600;letter-spacing:1px">VELORIN AKADEMIE GMBH.</div>
<div class="a f-line" style="top:3261px;line-height:17px">Lindenweg 9<br>4052 Talheim</div>
<div class="a f-line" style="top:3308px;line-height:17px">TEL: 061 555 01 23<br>info@velorin-akademie.ch</div>
<div class="a f-head">NOCH FRAGEN, ANREGUNGEN?<br>SCHREIBEN SIE UNS!</div>
<div class="a field" style="left:623px;top:3134px;width:330px;height:31px">NAME</div>
<div class="a field" style="left:623px;top:3180px;width:330px;height:30px">E-MAIL ADRESSE</div>
<div class="a field" style="left:623px;top:3221px;width:330px;height:101px;align-items:flex-start;padding-top:10px">NACHRICHT</div>
<div class="a btn" style="left:623px;top:3337px;width:164px;height:34px">SENDEN</div>

<div class="a bottom-bar"></div>
<div class="a bar-text" style="left:191px">Datenschutz</div>
<div class="a bar-text" style="left:311px">Impressum</div>
<div class="a bar-text" style="left:532px">VELORIN AKADEMIE | 2019</div>

<div class="a veil"></div>

<!-- Anmeldungsformular -->
<div class="a modal">
  <div class="a m-head"></div>
  <div class="a m-title">ANMELDUNGSFORMULAR</div>
  <div class="a m-close">X</div>
  <div class="a m-facts"></div>
  <div class="a m-label" style="left:105px;top:115px">SEMINAR</div><div class="a m-value" style="left:197px;top:115px">Zeit und Alternativen</div>
  <div class="a m-label" style="left:105px;top:141px">KOSTEN</div><div class="a m-value" style="left:197px;top:141px">CHF 280.-</div>
  <div class="a m-label" style="left:105px;top:167px">ORT</div><div class="a m-value" style="left:197px;top:167px">Schloss Auenrain</div>
  <div class="a m-label" style="left:105px;top:193px">DATUM</div><div class="a m-value" style="left:197px;top:193px">11. Mai 2019.</div>
  <div class="a m-strip"></div>
  <div class="a m-form"></div>
  <div class="a m-field" style="left:105px;top:271px;width:42px;height:23px">ANREDE</div>
  <div class="a m-field" style="left:159px;top:271px;width:152px;height:23px">NAME*</div>
  <div class="a m-field" style="left:322px;top:271px;width:187px;height:23px">VORNAME*</div>
  <div class="a m-field" style="left:105px;top:304px;width:206px;height:25px">E-MAIL ADRESSE*</div>
  <div class="a m-field" style="left:322px;top:304px;width:187px;height:25px">TELEFON</div>
  <div class="a m-field" style="left:105px;top:340px;width:347px;height:24px">STRASSE</div>
  <div class="a m-field" style="left:462px;top:340px;width:47px;height:24px">NR.</div>
  <div class="a m-field" style="left:105px;top:375px;width:47px;height:23px">PLZ</div>
  <div class="a m-field" style="left:159px;top:375px;width:350px;height:23px">ORT</div>
  <div class="a m-note" style="left:105px;top:405px">* gekennzeichneten Felder sind Pflichtfelder</div>
  <div class="a m-foot"></div>
  <div class="a" style="left:206px;top:438px;width:8px;height:8px;background:#fff"></div>
  <div class="a m-note" style="left:220px;top:439px">ich akzeptiere die Allgemeinen Geschäftsbedingungen</div>
  <div class="a m-btn" style="left:206px;top:460px;width:165px;height:32px">ANMELDEN</div>
</div>
</body>
</html>
```